Postcard Design

We are a High intensity gym in need of a postcard that shows a possible picture of one of our coaches coaching. Corvane’s mission is to bring high intensity, results-oriented workouts to the heart of Baltimore’s Inner Harbor. This is more than just a gym – our goal is to inspire, educate, and bring fun, functional workouts to everyone! IIt doesn't have to say all of that but it does need our information and where to find us. Plus, an offer for 2 weeks free if they text the word "Perform" to 41382. Which should be the main focal point.And our corvaneperformance.com and facebook info.

Target Market(s)

Fitness, women and men ages 20-60

Industry/Entity Type

Gym

Requirements
Must have
• REMOVE DYNAVOLT FROM THE TOP OF MY LOGO

```html
<!DOCTYPE html>
<html lang="en">
<head>
<meta charset="utf-8">
<title>Corvane Performance Center – Postcard</title>
<link rel="stylesheet" href="https://fonts.googleapis.com/css2?family=Bebas+Neue&family=Quicksand:wght@400;500;700&display=swap">
<style>
  :root {
    --paper: #ffffff;
    --ink: #111111;
    --muted: #3a3a3a;
    --photo-dark: #1c1c1c;
    --photo-mid: #4a4a48;
    --photo-light: #8a8884;
    --band: rgba(15, 15, 15, 0.88);
    --accent: #f2e21a;
    --headline-light: #f4f4f4;
    --mark: #2a2a2a;
  }
  * { margin: 0; padding: 0; box-sizing: border-box; }
  html, body { width: 1200px; height: 930px; overflow: hidden; background: var(--paper); }
  .postcard { position: relative; width: 1200px; height: 930px; background: var(--paper); }

  .promo-panel { position: absolute; left: 0; top: 0; width: 580px; height: 765px; overflow: hidden; }
  .promo-photo {
    position: absolute; inset: 0;
    background: radial-gradient(ellipse at 60% 45%, var(--photo-light) 0%, var(--photo-mid) 40%, var(--photo-dark) 85%);
  }
  .promo-lines { position: absolute; inset: 0; }

  .wellness-band {
    position: absolute; left: 95px; top: 42px; width: 485px; height: 93px;
    background: var(--band);
    clip-path: polygon(28px 0, 100% 0, 100% 100%, 0 100%);
  }
  .wellness-copy {
    position: absolute; right: 15px; top: 40px;
    font-family: "Quicksand", sans-serif; color: var(--headline-light);
  }
  .wellness-copy .lead { display: block; font-weight: 400; font-size: 30px; line-height: 1.15; }
  .wellness-copy .program { display: block; font-weight: 700; font-size: 29px; line-height: 1.2; }

  .headline {
    position: absolute; right: 22px; top: 296px; text-align: right;
    font-family: "Bebas Neue", sans-serif; font-weight: 400; font-size: 86px; line-height: 0.98;
    letter-spacing: 1px;
  }
  .headline span { display: block; }
  .headline .light { color: var(--headline-light); }
  .headline .accent { color: var(--accent); }

  .phone {
    position: absolute; right: 22px; top: 682px;
    font-family: "Bebas Neue", sans-serif; font-size: 74px; line-height: 1;
    color: var(--headline-light); letter-spacing: 1px;
  }

  .return-address {
    position: absolute; left: 600px; top: 100px; width: 280px; text-align: center;
    font-family: "Quicksand", sans-serif; font-style: normal; font-weight: 500; font-size: 20px;
    line-height: 40px; color: var(--ink);
  }

  .brand { position: absolute; left: 925px; top: 45px; width: 220px; text-align: center; }
  .brand-dot {
    display: block; width: 190px; height: 190px; margin: 0 auto;
    border-radius: 50%; background: var(--mark);
  }
  .brand-name {
    display: block; margin-top: 12px;
    font-family: "Quicksand", sans-serif; font-weight: 700; font-size: 44px;
    letter-spacing: 2px; color: var(--mark); line-height: 1;
  }

  .offer {
    position: absolute; left: 620px; top: 340px; width: 540px; text-align: center;
    font-family: "Quicksand", sans-serif; color: var(--ink);
  }
  .offer-title {
    display: inline-block; padding: 6px 26px 0;
    font-family: "Bebas Neue", sans-serif; font-weight: 400; font-size: 96px; line-height: 1;
    background: var(--accent); color: var(--ink); letter-spacing: 2px;
  }
  .offer-action {
    margin-top: 18px; font-weight: 500; font-size: 30px; line-height: 1.25;
  }
  .offer-action strong { font-weight: 700; }

  .online {
    position: absolute; left: 620px; top: 580px; width: 540px; text-align: center;
    font-family: "Quicksand", sans-serif; font-weight: 500; font-size: 20px; line-height: 34px;
    color: var(--muted);
  }
  .online strong { font-weight: 700; color: var(--ink); }
</style>
</head>
<body>
<main class="postcard">
  <section class="promo-panel">
    <div class="promo-photo" role="img" aria-label="Photo of a coach leading a group of adults through a dowel mobility drill inside the gym"></div>
    <svg class="promo-lines" width="580" height="765" viewBox="0 0 580 765" aria-hidden="true">
      <polyline points="0,712 105,712 120,662 580,662" fill="none" stroke="var(--accent)" stroke-width="4"/>
    </svg>
    <div class="wellness-band"></div>
    <p class="wellness-copy">
      <span class="lead">Ask us about our</span>
      <span class="program">Corporate Wellness Programs</span>
    </p>
    <h1 class="headline">
      <span class="light">Fun</span>
      <span class="accent">Educational</span>
      <span class="light">Motivating</span>
      <span class="accent">Workouts</span>
    </h1>
    <p class="phone">717-555-0148</p>
  </section>

  <address class="return-address">
    Corvane Performance Center<br>
    418 E. Harbor Row Suite 200<br>
    Baltimore, MD. 21202
  </address>

  <div class="brand">
    <span class="brand-dot"></span>
    <span class="brand-name">CORVANE</span>
  </div>

  <section class="offer">
    <h2 class="offer-title">2 Weeks Free</h2>
    <p class="offer-action">Text <strong>"Perform"</strong> to <strong>41382</strong></p>
  </section>

  <p class="online">
    <strong>corvaneperformance.com</strong><br>
    facebook.com/corvaneperformance
  </p>
</main>
</body>
</html>
```